SitePress Direct-Booking Website for Bend, Oregon Vacation Rental — $750 Budget
Project Overview

We are looking for a talented SitePress designer/developer to create a clean, professional and inviting direct-booking website for Birch Lantern Retreat, an established short-term vacation rental in Bend, Oregon.

The property is currently successfully listed on Staynest and Hoplo. Our Staynest property has approximately a 4.98-star rating with more than 200 reviews, is an Staynest Visitor Pick, and ranks among the Top 1% of eligible homes.

Project Budget: $750

We will select the designer based on the quality of the initial concept, understanding of the property, proposed booking solution and ability to deliver a completed and functioning SitePress website.

Existing Staynest Listing

Please use our current Staynest listing as the primary reference for photographs, property details, amenities and design inspiration:

https://www.staynest-example.net/rooms/48172036

Original high-resolution photographs and additional property information will be provided to the selected designer.

Design Direction

We want the website to feel:

Upscale but comfortable
Warm and welcoming
Clean and uncluttered
Pacific Northwest / Central Oregon
Professional rather than corporate
Highly visual with large property photographs
Easy to navigate
Excellent on phones, tablets and desktop computers

We welcome creativity and want designers to show us their vision for the property rather than simply copying our Staynest listing.

The website should immediately communicate that Birch Lantern Retreat is a highly rated vacation rental in an excellent Bend location.

Key Property Features
3 bedrooms
2 bathrooms
Sleeps up to 6 guests
Pet friendly
Approximately a 5-minute walk to Bend's Tannery Row Quarter
Near restaurants, shopping and Larkspur Fields Pavilion
Private fenced backyard
Covered outdoor area
Off-street driveway parking
Fireplace
Well-equipped kitchen
Staynest Prime Keeper
Staynest Visitor Pick
Top 1% of eligible Staynest homes
Approximately 4.98 stars with 200+ guest reviews

Our location, guest reviews, cleanliness, comfort, backyard, pet-friendly accommodations and walkability should be major selling points throughout the website.

Website Structure

We anticipate approximately 6–7 pages:

Home

Large hero photograph with a strong opening message and prominent BOOK DIRECT and CHECK AVAILABILITY buttons.

The home page should quickly communicate:

BIRCH LANTERN RETREAT — BEND, OREGON

3 Bedrooms | 2 Baths | Sleeps 6 | Pet Friendly | Walk to Tannery Row

Our exceptional guest rating and Staynest history should also be prominently featured.

The House

Bedrooms, bathrooms, kitchen, living areas, backyard and major amenities.

Photo Gallery

Large, attractive and fast-loading photographs with an easy-to-use mobile gallery.

Location / Explore Bend

Tannery Row Quarter, Larkspur Fields Pavilion, Deschutes River, restaurants, breweries, shopping, downtown Bend and nearby outdoor recreation.

Guest Reviews

Selected guest reviews and prominent presentation of our strong Staynest reputation.

Availability & Book Direct

A simple and professional direct-booking experience.

Contact / FAQ

Contact information plus common questions regarding pets, parking, check-in/check-out, cancellations and other policies.

IMPORTANT — Direct Booking & Credit Card Requirements

We want guests to be able to book directly through the website without having to contact us first.

The website should use a proven SitePress vacation-rental booking plugin or system rather than a custom-built reservation/payment system.

Guests should be able to:

Select arrival and departure dates
See available dates
Enter number of guests
See nightly charges
See cleaning fees
See applicable lodging taxes and other charges
See the complete reservation total before paying
Enter guest/contact information
Pay securely by credit or debit card
Receive an automatic reservation confirmation

Paywell is our preferred credit-card processor.

Credit-card information must be processed securely through Paywell or another established payment processor. Credit-card information should NOT be stored directly on our SitePress website.

Staynest & Hoplo Calendar Synchronization

This is very important.

The direct-booking calendar must synchronize with our existing Staynest and Hoplo calendars to reduce the possibility of double bookings.

For this single-property website, we prefer a simple solution using Staynest/Hoplo calendar or iCal synchronization rather than an expensive monthly channel-management service, if practical.

The designer should clearly identify the booking plugin/system they propose using.

IMPORTANT — Tell Us Your Proposed Booking Solution

As part of your submission, please tell us:

Which SitePress booking plugin/system you recommend.
Whether it synchronizes availability with Staynest and Hoplo.
Whether it integrates directly with Paywell.
The initial cost of the plugin/software.
Any annual or monthly fees.
Whether any additional paid software or services will be required.

We strongly prefer a solution with little or no ongoing monthly software expense.

We do not want to select a designer and later discover that the proposed booking system requires an expensive monthly subscription.

SitePress & Technical Requirements

The completed project should include:

Fully functioning SitePress website
Responsive desktop/tablet/mobile design
Fast-loading pages
Optimized photographs
SSL/HTTPS compatibility
Direct-booking functionality
Paywell payment integration
Staynest calendar synchronization
Hoplo calendar synchronization
Automatic booking confirmations
Cleaning fee and lodging-tax calculations
Contact form
Vizor Maps/location integration
Basic spam/security protection
Vizor Metrics capability
Basic SEO setup
Search-engine submission capability
Easy owner editing of text, rates and photographs
Search Engine Optimization

The website should be structured for Vizor and other search engines.

Important search themes include:

Bend Oregon vacation rental
Bend Oregon vacation home
Tannery Row Quarter vacation rental
Vacation rental near Tannery Row Bend
Bend Oregon pet-friendly vacation rental
Bend vacation rental near Larkspur Fields Pavilion
Bend Oregon direct booking vacation rental

We are not expecting an extensive ongoing SEO campaign for the $750 project. We do expect proper page titles, descriptions, headings, image optimization and a good technical foundation for future SEO.

Ownership

Upon completion and final payment:

We own the completed SitePress website.
We receive full SitePress administrator access.
We control the domain and hosting accounts.
We own all custom design files created for the project.
All necessary login credentials are provided to us.
The website can be moved to another SitePress hosting provider in the future.
There should be no proprietary dependency on the developer after completion.
What We Want From Contestants

Please review our Staynest listing before submitting your concept.

We are particularly interested in seeing an initial homepage concept showing how you would present:

Birch Lantern Retreat
The Bend / Tannery Row location
Our photography
Our exceptional guest reviews and ratings
The Book Direct message
The availability/booking call-to-action

We will provide feedback on the concepts we like and work with the selected designer to refine and complete the website.

Our Goal

Our objective is straightforward:

Create a beautiful, trustworthy and easy-to-use website that encourages guests to book Birch Lantern Retreat directly with us.

The website will complement—not replace—our existing Staynest and Hoplo listings.

We want repeat guests and new customers to have an easy way to find the property, check availability and book directly while receiving the same professional experience they expect from a major vacation-rental platform.

Target Market(s)

Consumers looking to to travel to Mexico for vacation. Family or couples

Industry/Entity Type

Short term vacation rental industry

Coding

Coded - Design and coding required

Number of Pages Required

5+ page

Requirements
Must have
• Capabilities to accept credit card payments and link to other rental property sites calendars such as HOPLO and Staynset
Nice to have
• Option for best plugins for property rental

```html
<!DOCTYPE html>
<html lang="en">
<head>
<meta charset="utf-8">
<title>Birch Lantern Retreat — Bend, Oregon</title>
<link href="https://fonts.googleapis.com/css2?family=Playfair+Display:wght@400;500&family=DM+Sans:wght@400;500;700&display=swap" rel="stylesheet">
<style>
:root{
  --board:#a9b5bf;
  --forest:#1c3329;
  --forest-deep:#14261e;
  --cream:#f4efe7;
  --card:#ffffff;
  --rust:#b95c3c;
  --ink:#1e2622;
  --muted:#6a6f6a;
  --line:#e2dcd2;
  --on-dark:#f3efe8;
}
*{box-sizing:border-box;margin:0;padding:0}
html,body{width:1200px;height:2735px;overflow:hidden;background:var(--board)}
body{font-family:"DM Sans",Arial,sans-serif;color:var(--ink);position:relative}
.serif{font-family:"Playfair Display",Georgia,serif;font-weight:400}
.abs{position:absolute}
.site{position:absolute;top:72px;height:2591px;background:var(--cream);overflow:hidden;box-shadow:0 6px 24px rgba(30,40,50,.18)}
.desktop{left:82px;width:818px}
.mobile{left:947px;width:170px}
.photo-house{background:linear-gradient(160deg,#2c3b36 0%,#3b3a30 35%,#6b4a2c 62%,#2a2a22 100%)}
.photo-hero{background:radial-gradient(ellipse at 62% 55%,rgba(190,120,60,.55),rgba(0,0,0,0) 45%),linear-gradient(180deg,#34463f 0%,#26352f 45%,#1e2a24 100%)}
.photo-living{background:radial-gradient(ellipse at 70% 65%,rgba(230,140,60,.6),rgba(0,0,0,0) 35%),linear-gradient(150deg,#7a5a3c,#4d3a2a 55%,#9a8a78)}
.photo-patio{background:linear-gradient(180deg,#56707a 0%,#3f4a3f 45%,#7a5a3a 75%,#3d4a30 100%)}
.label{font-size:6px;letter-spacing:.16em;font-weight:700;text-transform:uppercase;color:var(--forest)}
.btn{display:flex;align-items:center;justify-content:center;font-size:6.5px;font-weight:700;letter-spacing:.1em;text-transform:uppercase}
.btn-rust{background:var(--rust);color:#fff}
.btn-line{border:1px solid rgba(255,255,255,.8);color:#fff}
.btn-white{background:#fff;color:var(--ink)}
.brand{color:var(--on-dark);font-family:"Playfair Display",Georgia,serif;font-weight:400;font-size:9px;letter-spacing:.1em;text-transform:uppercase;white-space:nowrap}
.nav a{color:var(--on-dark);font-size:7px;text-decoration:none}
.on-dark{color:var(--on-dark)}
.field-label{font-size:5.5px;font-weight:700;letter-spacing:.1em;text-transform:uppercase;color:var(--ink)}
.field-val{font-size:7px;color:var(--muted)}
.feature{border-right:1px solid var(--line);text-align:center;padding-top:20px}
.feature:last-child{border-right:none}
.feature svg{width:18px;height:18px;stroke:var(--forest);fill:none;stroke-width:1.3}
.feature h4{font-size:6.5px;font-weight:700;letter-spacing:.04em;text-transform:uppercase;margin-top:7px}
.feature p{font-size:6px;color:var(--muted);line-height:1.5;margin:3px 12px 0}
.room{background:#fff}
.room h4{font-family:"Playfair Display",Georgia,serif;font-weight:400}
.room p{color:var(--muted)}
.step{border-right:1px solid var(--line);background:#fff}
.num{color:var(--rust);font-weight:700}
.stars{color:var(--rust);letter-spacing:1px}
</style>
</head>
<body>

<!-- ============ DESKTOP ============ -->
<div class="site desktop">
  <header class="abs photo-hero" style="left:0;top:0;width:818px;height:492px" role="img" aria-label="Craftsman-style timber house at dusk among tall pines, windows lit warmly"></header>
  <div class="abs brand" style="left:43px;top:18px">Birch Lantern Retreat</div>
  <nav class="abs nav" style="left:467px;top:18px;display:flex;gap:14px">
    <a>The House</a><a>Amenities</a><a>Gallery</a><a>Explore Bend</a><a>Reviews</a>
  </nav>
  <div class="abs btn btn-line" style="left:704px;top:11px;width:74px;height:24px">Book Direct</div>

  <div class="abs label on-dark" style="left:51px;top:151px">Bend, Oregon</div>
  <h1 class="abs serif on-dark" style="left:50px;top:170px;font-size:39px;line-height:43px;letter-spacing:-.5px">Your Bend getaway,<br>steps from Tannery Row.</h1>
  <p class="abs on-dark" style="left:51px;top:265px;font-size:8.5px;line-height:15px;width:290px">A stylish, comfortable home for making memories in the heart of Central Oregon.</p>
  <div class="abs btn btn-rust" style="left:51px;top:308px;width:101px;height:25px">Check Availability</div>
  <div class="abs btn btn-line" style="left:157px;top:308px;width:99px;height:25px">Explore the House</div>
  <p class="abs on-dark" style="left:51px;top:347px;font-size:7px">3 Bedrooms &nbsp;•&nbsp; 2 Baths &nbsp;•&nbsp; Sleeps 6 &nbsp;•&nbsp; Pet Friendly</p>
  <p class="abs on-dark" style="left:51px;top:366px;font-size:7px"><b style="font-size:9px">4.98 ★</b> &nbsp; 205+ Reviews &nbsp; Top 1% of homes</p>

  <form class="abs" style="left:74px;top:465px;width:670px;height:54px;background:#fff;box-shadow:0 6px 18px rgba(0,0,0,.12);display:flex;align-items:center;padding:0 10px 0 22px">
    <div style="width:157px;border-right:1px solid var(--line);padding-right:14px;margin-right:22px">
      <div class="field-label">Check In</div>
      <div class="field-val" style="margin-top:8px;display:flex;justify-content:space-between">dd/mm/yyyy<span>▭</span></div>
    </div>
    <div style="width:157px;border-right:1px solid var(--line);padding-right:14px;margin-right:22px">
      <div class="field-label">Check Out</div>
      <div class="field-val" style="margin-top:8px;display:flex;justify-content:space-between">dd/mm/yyyy<span>▭</span></div>
    </div>
    <div style="width:150px;padding-right:8px">
      <div class="field-label">Guests</div>
      <div class="field-val" style="margin-top:8px;display:flex;justify-content:space-between">1 guest<span>⌄</span></div>
    </div>
    <div class="btn btn-rust" style="margin-left:auto;width:101px;height:25px">Check Availability</div>
  </form>

  <!-- intro -->
  <div class="abs label" style="left:75px;top:624px">Welcome to Birch Lantern Retreat</div>
  <h2 class="abs serif" style="left:74px;top:639px;font-size:30px;line-height:33px">Thoughtful<br>comfort in the<br>perfect location.</h2>
  <p class="abs" style="left:75px;top:752px;width:240px;font-size:7.2px;line-height:13px;color:#3f4540">Settle into a beautifully appointed three-bedroom home near Bend's Tannery Row Quarter. Bright gathering spaces, restful bedrooms and a private backyard make it an easy base for days outside and evenings together.</p>
  <div class="abs" style="left:75px;top:819px;font-size:6.5px;font-weight:700;letter-spacing:.1em">DISCOVER THE HOUSE →</div>
  <div class="abs photo-living" style="left:360px;top:581px;width:247px;height:290px" role="img" aria-label="Living room with stone fireplace, leather sofas and timber coffee table"></div>
  <div class="abs photo-living" style="left:613px;top:581px;width:132px;height:142px" role="img" aria-label="Living room corner with lit fireplace and tall windows"></div>
  <div class="abs photo-patio" style="left:613px;top:729px;width:132px;height:142px" role="img" aria-label="Covered back patio with lounge seating and lawn at dusk"></div>

  <!-- features -->
  <div class="abs" style="left:77px;top:931px;width:664px;height:99px;background:#f7f4ee;border:1px solid var(--line);display:grid;grid-template-columns:repeat(6,1fr)">
    <div class="feature"><svg viewBox="0 0 20 20"><circle cx="6" cy="6" r="2"/><circle cx="14" cy="6" r="2"/><circle cx="3.5" cy="11" r="1.8"/><circle cx="16.5" cy="11" r="1.8"/><path d="M6 16c0-3 2-5 4-5s4 2 4 5c0 2-8 2-8 0z"/></svg><h4>Pet Friendly</h4><p>Fenced yard and room to relax.</p></div>
    <div class="feature"><svg viewBox="0 0 20 20"><path d="M10 18s6-6 6-10a6 6 0 0 0-12 0c0 4 6 10 6 10z"/><circle cx="10" cy="8" r="2"/></svg><h4>Walk to Tannery Row</h4><p>Dining, shops and river paths nearby.</p></div>
    <div class="feature"><svg viewBox="0 0 20 20"><circle cx="10" cy="11" r="7"/><path d="M10 15c-2 0-3-1.5-3-3 0-2 3-4 3-6 1 2 3 3 3 6 0 1.5-1 3-3 3z"/></svg><h4>Outdoor Living</h4><p>Covered patio and fire-pit table.</p></div>
    <div class="feature"><svg viewBox="0 0 20 20"><circle cx="8" cy="8" r="3"/><path d="M8 1v2M8 13v2M1 8h2M13 8h2M3 3l1.5 1.5M11.5 11.5L13 13M13 3l-1.5 1.5M3 13l1.5-1.5"/><path d="M16 12v5M14.5 14.5h3"/></svg><h4>Year-Round Comfort</h4><p>Fireplace, heating and air conditioning.</p></div>
    <div class="feature"><svg viewBox="0 0 20 20"><path d="M2 8a12 12 0 0 1 16 0M5 11a7.5 7.5 0 0 1 10 0M8 14a3 3 0 0 1 4 0"/><circle cx="10" cy="16.5" r=".8"/></svg><h4>Fast Wi-Fi</h4><p>Reliable connection throughout.</p></div>
    <div class="feature"><svg viewBox="0 0 20 20"><path d="M3 12l2-5h10l2 5v4H3z"/><path d="M3 12h14"/><circle cx="6" cy="14" r=".8"/><circle cx="14" cy="14" r=".8"/></svg><h4>Easy Parking</h4><p>Dedicated off-street driveway.</p></div>
  </div>

  <!-- location band -->
  <section class="abs" style="left:0;top:1082px;width:818px;height:276px;background:var(--forest)">
    <div class="abs photo-house" style="left:0;top:0;width:372px;height:276px" role="img" aria-label="Front of the timber home at twilight with glowing windows and pines"></div>
    <div class="abs label on-dark" style="left:430px;top:57px;opacity:.85">The best of Bend, close by</div>
    <h2 class="abs serif on-dark" style="left:429px;top:73px;font-size:31px;line-height:34px">A short walk to the<br>Tannery Row Quarter.</h2>
    <p class="abs on-dark" style="left:430px;top:154px;font-size:7.2px;line-height:13px;width:300px;opacity:.9">Follow the Deschutes River, catch a show at Larkspur Fields Pavilion, browse local shops or choose a table at one of Bend's favorite restaurants.</p>
    <div class="abs btn btn-line" style="left:430px;top:197px;width:79px;height:25px">Explore Bend</div>
  </section>

  <!-- reviews -->
  <div class="abs label" style="left:75px;top:1420px">Guest Love</div>
  <h2 class="abs serif" style="left:74px;top:1437px;font-size:28px;line-height:33px">What our<br>guests are<br>saying</h2>
  <blockquote class="abs" style="left:321px;top:1425px;width:424px;height:117px;background:#fff;border:1px solid var(--line);padding:30px 32px 0">
    <p class="serif" style="font-size:11px;line-height:19px">“Perfect location, beautiful home and thoughtful details. We walked to Tannery Row and loved relaxing by the backyard fire.”</p>
    <div style="display:flex;justify-content:space-between;margin-top:12px;font-size:5.8px;font-weight:700;letter-spacing:.1em"><span>RECENT GUEST REVIEW</span><span class="stars" style="font-size:7px">★★★★★</span></div>
  </blockquote>

  <!-- rooms -->
  <div class="abs label" style="left:75px;top:1620px">Rooms &amp; Spaces</div>
  <h2 class="abs serif" style="left:74px;top:1635px;font-size:30px;line-height:33px">Room to rest, gather and<br>recharge.</h2>
  <div class="abs room" style="left:75px;top:1725px;width:216px;height:198px"><div class="photo-living" style="height:147px" role="img" aria-label="Primary suite lounge with fireplace"></div><h4 style="font-size:11px;margin:11px 0 0 12px">Primary Suite</h4><p style="font-size:7px;margin:3px 0 0 12px">King bed · restful retreat</p></div>
  <div class="abs room" style="left:302px;top:1725px;width:216px;height:198px"><div class="photo-patio" style="height:147px" role="img" aria-label="Backyard patio and lawn at dusk"></div><h4 style="font-size:11px;margin:11px 0 0 12px">Guest Bedroom</h4><p style="font-size:7px;margin:3px 0 0 12px">Queen bed · soft natural light</p></div>
  <div class="abs room" style="left:529px;top:1725px;width:216px;height:198px"><div class="photo-house" style="height:147px" role="img" aria-label="Exterior of the house among pines at twilight"></div><h4 style="font-size:11px;margin:11px 0 0 12px">Third Bedroom</h4><p style="font-size:7px;margin:3px 0 0 12px">Comfortable space for two</p></div>

  <!-- explore -->
  <div class="abs label" style="left:75px;top:1996px">Explore Bend</div>
  <h2 class="abs serif" style="left:74px;top:2011px;font-size:30px;line-height:33px">Adventure begins at your<br>doorstep.</h2>
  <div class="abs" style="left:75px;top:2100px;width:670px;height:135px;display:grid;grid-template-columns:repeat(4,1fr)">
    <div class="step" style="padding:20px 19px"><div class="num" style="font-size:7px">01</div><h4 class="serif" style="font-size:12px;margin-top:28px">River &amp; trails</h4><p style="font-size:7px;color:var(--muted);line-height:13px;margin-top:6px">Walk, paddle or bike along the Deschutes.</p></div>
    <div class="step" style="padding:20px 19px"><div class="num" style="font-size:7px">02</div><h4 class="serif" style="font-size:12px;margin-top:28px">Food &amp; breweries</h4><p style="font-size:7px;color:var(--muted);line-height:13px;margin-top:6px">Discover Bend's relaxed local flavor.</p></div>
    <div class="step" style="padding:20px 19px"><div class="num" style="font-size:7px">03</div><h4 class="serif" style="font-size:12px;margin-top:28px">Live music</h4><p style="font-size:7px;color:var(--muted);line-height:13px;margin-top:6px">Summer nights at the pavilion.</p></div>
    <div class="step" style="padding:20px 19px;border-right:none"><div class="num" style="font-size:7px">04</div><h4 class="serif" style="font-size:12px;margin-top:28px">Mountain days</h4><p style="font-size:7px;color:var(--muted);line-height:13px;margin-top:6px">Easy access to Central Oregon scenery.</p></div>
  </div>

  <!-- cta -->
  <section class="abs" style="left:0;top:2295px;width:818px;height:134px;background:var(--rust)">
    <div class="abs label on-dark" style="left:57px;top:37px">Plan your stay</div>
    <h2 class="abs serif on-dark" style="left:57px;top:50px;font-size:27px">Ready for your Bend getaway?</h2>
    <p class="abs on-dark" style="left:57px;top:89px;font-size:7px">Book direct for a simple, personal reservation experience.</p>
    <div class="abs btn btn-white" style="left:662px;top:55px;width:100px;height:24px">Check Availability</div>
  </section>

  <!-- footer -->
  <footer class="abs" style="left:0;top:2429px;width:818px;height:162px;background:var(--forest)">
    <div class="abs brand" style="left:49px;top:38px">Birch Lantern Retreat</div>
    <p class="abs on-dark" style="left:49px;top:62px;font-size:7.5px">Your welcoming home base in Bend, Oregon.</p>
    <nav class="abs nav" style="left:49px;top:92px;display:flex;gap:13px"><a>The House</a><a>Explore Bend</a><a>Reviews</a><a>Contact</a></nav>
    <div class="abs" style="left:49px;top:120px;width:722px;height:1px;background:rgba(255,255,255,.15)"></div>
    <p class="abs on-dark" style="left:49px;top:134px;font-size:5.5px;opacity:.8">© 2026 Birch Lantern Retreat. All rights reserved.</p>
  </footer>
</div>

<!-- ============ MOBILE ============ -->
<div class="site mobile">
  <header class="abs photo-hero" style="left:0;top:0;width:170px;height:254px" role="img" aria-label="Timber house at dusk among tall pines"></header>
  <div class="abs brand" style="left:10px;top:9px;font-size:5px">Birch Lantern Retreat</div>
  <div class="abs on-dark" style="left:155px;top:8px;font-size:6px">≡</div>
  <div class="abs label on-dark" style="left:8px;top:69px;font-size:3.5px">Bend, Oregon</div>
  <h1 class="abs serif on-dark" style="left:8px;top:80px;font-size:14.5px;line-height:16px;letter-spacing:-.3px">Your Bend getaway,<br>steps from Tannery Row.</h1>
  <p class="abs on-dark" style="left:8px;top:122px;font-size:5px;line-height:9px;width:150px">A stylish, comfortable home for making memories in the heart of Central Oregon.</p>
  <div class="abs btn btn-rust" style="left:8px;top:152px;width:67px;height:14px;font-size:3.6px">Check Availability</div>
  <div class="abs btn btn-line" style="left:8px;top:172px;width:67px;height:14px;font-size:3.6px">Explore the House</div>
  <p class="abs on-dark" style="left:8px;top:200px;font-size:4px">3 Bedrooms • 2 Baths • Sleeps 6 • Pet Friendly</p>
  <p class="abs on-dark" style="left:8px;top:212px;font-size:4px"><b style="font-size:5px">4.98 ★</b> 205+ Reviews &nbsp;Top 1% of homes</p>

  <form class="abs" style="left:6px;top:254px;width:158px;height:120px;background:#fff;box-shadow:0 4px 10px rgba(0,0,0,.1);padding:10px 12px 0">
    <div class="field-label" style="font-size:3.4px">Check In</div>
    <div class="field-val" style="font-size:4.3px;margin-top:3px;padding-bottom:5px;border-bottom:1px solid var(--line);display:flex;justify-content:space-between">dd/mm/yyyy<span>▭</span></div>
    <div class="field-label" style="font-size:3.4px;margin-top:5px">Check Out</div>
    <div class="field-val" style="font-size:4.3px;margin-top:3px;padding-bottom:5px;border-bottom:1px solid var(--line);display:flex;justify-content:space-between">dd/mm/yyyy<span>▭</span></div>
    <div class="field-label" style="font-size:3.4px;margin-top:5px">Guests</div>
    <div class="field-val" style="font-size:4.3px;margin-top:3px;padding-bottom:5px;border-bottom:1px solid var(--line);display:flex;justify-content:space-between">1 guest<span>⌄</span></div>
    <div class="btn btn-rust" style="margin-top:8px;height:15px;font-size:3.6px">Check Availability</div>
  </form>

  <div class="abs label" style="left:8px;top:403px;font-size:3.4px">Welcome to Birch Lantern Retreat</div>
  <h2 class="abs serif" style="left:8px;top:413px;font-size:12.5px;line-height:15px">Thoughtful comfort in the<br>perfect location.</h2>
  <p class="abs" style="left:8px;top:450px;width:152px;font-size:4.3px;line-height:8.5px;color:#3f4540">Settle into a beautifully appointed three-bedroom home near Bend's Tannery Row Quarter. Bright gathering spaces, restful bedrooms and a private backyard make it an easy base for days outside and evenings together.</p>
  <div class="abs" style="left:8px;top:498px;font-size:3.6px;font-weight:700;letter-spacing:.08em">DISCOVER THE HOUSE →</div>
  <div class="abs photo-living" style="left:8px;top:521px;width:154px;height:113px" role="img" aria-label="Living room with stone fireplace"></div>
  <div class="abs photo-living" style="left:8px;top:637px;width:75px;height:61px" role="img" aria-label="Fireplace corner with windows"></div>
  <div class="abs photo-patio" style="left:86px;top:637px;width:76px;height:61px" role="img" aria-label="Covered patio at dusk"></div>

  <div class="abs" style="left:11px;top:727px;width:148px;height:200px;display:grid;grid-template-columns:1fr 1fr;grid-template-rows:repeat(3,1fr);background:#f7f4ee;border:1px solid var(--line)">
    <div class="feature" style="padding-top:13px;border-bottom:1px solid var(--line)"><svg style="width:11px;height:11px" viewBox="0 0 20 20"><circle cx="6" cy="6" r="2"/><circle cx="14" cy="6" r="2"/><circle cx="3.5" cy="11" r="1.8"/><circle cx="16.5" cy="11" r="1.8"/><path d="M6 16c0-3 2-5 4-5s4 2 4 5c0 2-8 2-8 0z"/></svg><h4 style="font-size:3.6px;margin-top:4px">Pet Friendly</h4><p style="font-size:3.3px;margin:2px 6px 0">Fenced yard and room to relax.</p></div>
    <div class="feature" style="padding-top:13px;border-bottom:1px solid var(--line);border-right:none"><svg style="width:11px;height:11px" viewBox="0 0 20 20"><path d="M10 18s6-6 6-10a6 6 0 0 0-12 0c0 4 6 10 6 10z"/><circle cx="10" cy="8" r="2"/></svg><h4 style="font-size:3.6px;margin-top:4px">Walk to Tannery Row</h4><p style="font-size:3.3px;margin:2px 6px 0">Dining, shops and river paths nearby.</p></div>
    <div class="feature" style="padding-top:13px;border-bottom:1px solid var(--line)"><svg style="width:11px;height:11px" viewBox="0 0 20 20"><circle cx="10" cy="11" r="7"/><path d="M10 15c-2 0-3-1.5-3-3 0-2 3-4 3-6 1 2 3 3 3 6 0 1.5-1 3-3 3z"/></svg><h4 style="font-size:3.6px;margin-top:4px">Outdoor Living</h4><p style="font-size:3.3px;margin:2px 6px 0">Covered patio and fire-pit table.</p></div>
    <div class="feature" style="padding-top:13px;border-bottom:1px solid var(--line);border-right:none"><svg style="width:11px;height:11px" viewBox="0 0 20 20"><circle cx="8" cy="8" r="3"/><path d="M8 1v2M8 13v2M1 8h2M13 8h2"/><path d="M16 12v5M14.5 14.5h3"/></svg><h4 style="font-size:3.6px;margin-top:4px">Year-Round Comfort</h4><p style="font-size:3.3px;margin:2px 6px 0">Fireplace, heating and air conditioning.</p></div>
    <div class="feature" style="padding-top:13px"><svg style="width:11px;height:11px" viewBox="0 0 20 20"><path d="M2 8a12 12 0 0 1 16 0M5 11a7.5 7.5 0 0 1 10 0M8 14a3 3 0 0 1 4 0"/></svg><h4 style="font-size:3.6px;margin-top:4px">Fast Wi-Fi</h4><p style="font-size:3.3px;margin:2px 6px 0">Reliable connection throughout.</p></div>
    <div class="feature" style="padding-top:13px;border-right:none"><svg style="width:11px;height:11px" viewBox="0 0 20 20"><path d="M3 12l2-5h10l2 5v4H3z"/><path d="M3 12h14"/></svg><h4 style="font-size:3.6px;margin-top:4px">Easy Parking</h4><p style="font-size:3.3px;margin:2px 6px 0">Dedicated off-street driveway.</p></div>
  </div>

  <div class="abs photo-house" style="left:0;top:950px;width:170px;height:132px" role="img" aria-label="Timber home exterior at twilight"></div>
  <section class="abs" style="left:0;top:1082px;width:170px;height:149px;background:var(--forest)">
    <div class="abs label on-dark" style="left:8px;top:25px;font-size:3.4px">The best of Bend, close by</div>
    <h2 class="abs serif on-dark" style="left:8px;top:34px;font-size:13px;line-height:15px">A short walk to the<br>Tannery Row Quarter.</h2>
    <p class="abs on-dark" style="left:8px;top:68px;width:155px;font-size:4.2px;line-height:8px">Follow the Deschutes River, catch a show at Larkspur Fields Pavilion, browse local shops or choose a table at one of Bend's favorite restaurants.</p>
    <div class="abs btn btn-line" style="left:8px;top:112px;width:53px;height:15px;font-size:3.5px">Explore Bend</div>
  </section>

  <div class="abs label" style="left:8px;top:1259px;font-size:3.4px">Guest Love</div>
  <h2 class="abs serif" style="left:8px;top:1268px;font-size:11.5px">What our guests are saying</h2>
  <blockquote class="abs" style="left:8px;top:1302px;width:154px;height:88px;background:#fff;border:1px solid var(--line);padding:12px 9px 0">
    <p class="serif" style="font-size:7px;line-height:12.5px">“Perfect location, beautiful home and thoughtful details. We walked to Tannery Row and loved relaxing by the backyard fire.”</p>
    <div style="display:flex;justify-content:space-between;margin-top:4px;font-size:3.3px;font-weight:700;letter-spacing:.08em"><span>RECENT GUEST REVIEW</span><span class="stars" style="font-size:4px">★★★★★</span></div>
  </blockquote>

  <div class="abs label" style="left:8px;top:1448px;font-size:3.4px">Rooms &amp; Spaces</div>
  <h2 class="abs serif" style="left:8px;top:1457px;font-size:12px;line-height:14.5px">Room to rest, gather and<br>recharge.</h2>
  <div class="abs room" style="left:8px;top:1502px;width:154px;height:123px"><div class="photo-living" style="height:88px" role="img" aria-label="Primary suite lounge"></div><h4 style="font-size:7px;margin:8px 0 0 8px">Primary Suite</h4><p style="font-size:4px;margin:2px 0 0 8px">King bed · restful retreat</p></div>
  <div class="abs room" style="left:8px;top:1632px;width:154px;height:123px"><div class="photo-patio" style="height:88px" role="img" aria-label="Backyard patio at dusk"></div><h4 style="font-size:7px;margin:8px 0 0 8px">Guest Bedroom</h4><p style="font-size:4px;margin:2px 0 0 8px">Queen bed · soft natural light</p></div>
  <div class="abs room" style="left:8px;top:1763px;width:154px;height:123px"><div class="photo-house" style="height:88px" role="img" aria-label="House exterior among pines"></div><h4 style="font-size:7px;margin:8px 0 0 8px">Third Bedroom</h4><p style="font-size:4px;margin:2px 0 0 8px">Comfortable space for two</p></div>

  <div class="abs label" style="left:8px;top:1942px;font-size:3.4px">Explore Bend</div>
  <h2 class="abs serif" style="left:8px;top:1951px;font-size:12px;line-height:14.5px">Adventure begins at your<br>doorstep.</h2>
  <div class="abs" style="left:8px;top:1997px;width:154px;height:335px;display:grid;grid-template-rows:repeat(4,1fr);background:#fff">
    <div style="padding:10px 13px;border-bottom:1px solid var(--line)"><div class="num" style="font-size:4px">01</div><h4 class="serif" style="font-size:7.5px;margin-top:18px">River &amp; trails</h4><p style="font-size:4px;color:var(--muted);margin-top:5px">Walk, paddle or bike along the Deschutes.</p></div>
    <div style="padding:10px 13px;border-bottom:1px solid var(--line)"><div class="num" style="font-size:4px">02</div><h4 class="serif" style="font-size:7.5px;margin-top:18px">Food &amp; breweries</h4><p style="font-size:4px;color:var(--muted);margin-top:5px">Discover Bend's relaxed local flavor.</p></div>
    <div style="padding:10px 13px;border-bottom:1px solid var(--line)"><div class="num" style="font-size:4px">03</div><h4 class="serif" style="font-size:7.5px;margin-top:18px">Live music</h4><p style="font-size:4px;color:var(--muted);margin-top:5px">Summer nights at the pavilion.</p></div>
    <div style="padding:10px 13px"><div class="num" style="font-size:4px">04</div><h4 class="serif" style="font-size:7.5px;margin-top:18px">Mountain days</h4><p style="font-size:4px;color:var(--muted);margin-top:5px">Easy access to Central Oregon scenery.</p></div>
  </div>

  <section class="abs" style="left:0;top:2359px;width:170px;height:124px;background:var(--rust)">
    <div class="abs label on-dark" style="left:12px;top:24px;font-size:3.4px">Plan your stay</div>
    <h2 class="abs serif on-dark" style="left:12px;top:33px;font-size:11px;line-height:13px">Ready for your Bend<br>getaway?</h2>
    <p class="abs on-dark" style="left:12px;top:64px;font-size:4px">Book direct for a simple, personal reservation experience.</p>
    <div class="abs btn btn-white" style="left:12px;top:83px;width:68px;height:15px;font-size:3.5px">Check Availability</div>
  </section>

  <footer class="abs" style="left:0;top:2483px;width:170px;height:108px;background:var(--forest)">
    <div class="abs brand" style="left:10px;top:23px;font-size:5px">Birch Lantern Retreat</div>
    <p class="abs on-dark" style="left:10px;top:37px;font-size:3.8px">Your welcoming home base in Bend, Oregon.</p>
    <nav class="abs nav" style="left:10px;top:52px;display:flex;gap:8px"><a style="font-size:3.8px">The House</a><a style="font-size:3.8px">Explore Bend</a><a style="font-size:3.8px">Reviews</a><a style="font-size:3.8px">Contact</a></nav>
    <div class="abs" style="left:10px;top:65px;width:150px;height:1px;background:rgba(255,255,255,.15)"></div>
    <p class="abs on-dark" style="left:10px;top:71px;font-size:3px;opacity:.8">© 2026 Birch Lantern Retreat. All rights reserved.</p>
  </footer>
</div>

</body>
</html>
```